Building company buisness cards

We are looking for a sharp modern new look for our business cards.
We are a New Zealand based company that specialises in house and land packages.
We have attached a photo of the current logo and would like to see if it can be improved somehow if needed.
We are open to any colours but we have chosen green at this stage.
Feel free to change the font and make the logo smarter looking.
Play with the colours and see what looks best.

We want a card that looks so good know one will want to throw it away!

Target Market(s)

Home buyers

Industry/Entity Type

Building

Contact Information for Business Card

Derek Tolvane
0217394062
dtolvane@quillmarkhomesteads.co.nz
quillmarkhomesteads.co.nz

Font styles to use
Serif
Sans Serif

Colors

Designer to choose colors to be used in the design.

Requirements
Must have
• Logo and company name on one side, details on the other side
Nice to have
• Color codes for the original green are HEX #4a8028, RGB(74,128,40), CMYK(42,0,69,50)
• Round corners, Raised and/or spot UV

```html
<!DOCTYPE html>
<html lang="en">
<head>
<meta charset="utf-8">
<title>Quillmark Homesteads – Business Card</title>
<link rel="stylesheet" href="https://fonts.googleapis.com/css2?family=Montserrat:wght@400;500;800&display=swap">
<style>
  :root {
    --stage: #e9e6e2;
    --brand-blue: #0f4aa3;
    --brand-blue-deep: #0a3a86;
    --brand-green: #9cc42b;
    --card-white: #fbfbfb;
    --ink: #3d3d3d;
    --muted: #6a6a6a;
    --faint: #e6e6e6;
  }
  * { box-sizing: border-box; margin: 0; padding: 0; }
  html, body { width: 1200px; height: 1021px; overflow: hidden; }
  body {
    background: var(--stage);
    font-family: "Montserrat", sans-serif;
    position: relative;
  }
  .card {
    position: absolute;
    width: 700px;
    height: 400px;
    border-radius: 26px;
    overflow: hidden;
    box-shadow: 0 10px 24px rgba(0,0,0,0.18);
  }

  /* Logo side */
  .card-back {
    left: 420px;
    top: 60px;
    background: var(--brand-blue);
  }
  .back-pattern {
    position: absolute;
    inset: 0;
    background: linear-gradient(125deg, #3a6cc0 0%, #1a55b0 40%, var(--brand-blue) 65%, var(--brand-blue-deep) 100%);
  }
  .back-lockup {
    position: absolute;
    left: 0; right: 0;
    top: 118px;
    display: flex;
    flex-direction: column;
    align-items: center;
    gap: 18px;
  }
  .back-mark {
    width: 62px;
    height: 62px;
    border-radius: 50%;
    background: #ffffff;
  }
  .back-wordmark {
    color: #ffffff;
    font-weight: 800;
    font-size: 46px;
    letter-spacing: -0.5px;
    line-height: 1;
  }

  /* Details side */
  .card-front {
    left: 80px;
    top: 540px;
    background: var(--card-white);
  }
  .front-decoration {
    position: absolute;
    right: 0;
    bottom: 0;
    width: 210px;
    height: 250px;
    background: linear-gradient(160deg, rgba(230,230,230,0) 0%, var(--faint) 45%, #e0e0e0 100%);
  }
  .side-band {
    position: absolute;
    left: 96px;
    width: 40px;
  }
  .side-band.blue { top: 0; height: 232px; background: var(--brand-blue); }
  .side-band.green { top: 232px; bottom: 0; background: var(--brand-green); }
  .contact-icons {
    position: absolute;
    left: 96px;
    top: 254px;
    width: 40px;
    display: flex;
    flex-direction: column;
    align-items: center;
    gap: 10px;
  }
  .front-wordmark {
    position: absolute;
    left: 166px;
    top: 64px;
    color: var(--brand-blue);
    font-weight: 800;
    font-size: 38px;
    letter-spacing: -0.5px;
    line-height: 1;
  }
  .holder {
    position: absolute;
    left: 166px;
    top: 178px;
  }
  .holder-name {
    color: var(--brand-blue);
    font-weight: 800;
    font-size: 26px;
  }
  .holder-role {
    color: var(--muted);
    font-size: 17px;
    margin-top: 2px;
  }
  .contact-list {
    position: absolute;
    left: 166px;
    top: 258px;
    list-style: none;
    color: var(--ink);
    font-size: 16px;
    line-height: 26px;
  }
</style>
</head>
<body>

  <section class="card card-back" aria-label="Card logo side">
    <div class="back-pattern" role="img" aria-label="Embossed repeating pattern of house motifs in shades of blue"></div>
    <div class="back-lockup">
      <span class="back-mark"></span>
      <div class="back-wordmark">Quillmark Homesteads</div>
    </div>
  </section>

  <section class="card card-front" aria-label="Card details side">
    <div class="front-decoration" role="img" aria-label="Large faint house motif in light grey"></div>
    <div class="side-band blue"></div>
    <div class="side-band green"></div>
    <div class="contact-icons" aria-hidden="true">
      <svg width="16" height="16" viewBox="0 0 16 16"><path d="M4 1.5 L6.2 4.5 L5 6 C5.8 8 8 10.2 10 11 L11.5 9.8 L14.5 12 L13 14.5 C7 14 2 9 1.5 3 Z" fill="#fff"/></svg>
      <svg width="18" height="14" viewBox="0 0 18 14"><rect x="1" y="1" width="16" height="12" fill="none" stroke="#fff" stroke-width="1.5"/><path d="M1 1 L9 8 L17 1" fill="none" stroke="#fff" stroke-width="1.5"/></svg>
      <svg width="17" height="17" viewBox="0 0 18 18"><circle cx="9" cy="9" r="7.5" fill="none" stroke="#fff" stroke-width="1.4"/><ellipse cx="9" cy="9" rx="3.2" ry="7.5" fill="none" stroke="#fff" stroke-width="1.2"/><path d="M1.5 9 H16.5 M3 5 H15 M3 13 H15" stroke="#fff" stroke-width="1.2"/></svg>
    </div>

    <div class="front-wordmark">Quillmark Homesteads</div>

    <div class="holder">
      <div class="holder-name">Derek Tolvane</div>
      <div class="holder-role">Founder</div>
    </div>

    <ul class="contact-list">
      <li>0217394062</li>
      <li>dtolvane@quillmarkhomesteads.co.nz</li>
      <li>quillmarkhomesteads.co.nz</li>
    </ul>
  </section>

</body>
</html>
```